Indy Film Production Company/Studio

We need a business card designed from an existing logo. We are a digital studio/production company that caters to creating genre entertainment, like Action, Horror, and martial arts. The card along with the logo will be used to Brand the company from letter heads to banners. The design will also be used for postcards and Brochures. It should be professional and masculine.
Updates

Thank you to all the designers who have participated. I'm narrowing down who it will be. Thank you again.

Target Market(s)

Investors, Networks, Producers, and actors

Industry/Entity Type

Film Production

Contact Information for Business Card

Teodoro Valbuena
Producer/Writer/Director
www.kestrelpicturehouse.example

Requirements
Must have
• Website address, Facebook icon and Twitter icon possibly in the back of the card.
Nice to have
• Logline of Company: Follow The Action.

```html
<!DOCTYPE html>
<html lang="en">
<head>
<meta charset="utf-8">
<title>Kestrel Picture House — Business Card</title>
<link rel="stylesheet" href="https://fonts.googleapis.com/css2?family=Open+Sans:wght@400;600;800&display=swap">
<style>
  :root {
    --backdrop: #3b322e;
    --card: #111111;
    --card-edge: #1c1c1c;
    --red: #e0202a;
    --white: #f2f2f2;
    --grey: #8a8a8a;
    --rule: #555555;
  }
  * { box-sizing: border-box; margin: 0; padding: 0; }
  html, body { width: 1200px; height: 814px; overflow: hidden; }
  body {
    background: var(--backdrop);
    font-family: "Open Sans", Arial, sans-serif;
    position: relative;
  }
  .card {
    position: absolute;
    top: 258px;
    width: 520px;
    height: 297px;
    background: var(--card);
    border: 1px solid var(--card-edge);
    box-shadow: 0 6px 18px rgba(0,0,0,.35);
    overflow: hidden;
  }
  .card--front { left: 50px; }
  .card--back { left: 630px; }

  /* brand wordmark */
  .brand { position: absolute; text-align: left; }
  .brand__initials {
    display: block;
    font-weight: 800;
    font-size: 58px;
    line-height: 1;
    letter-spacing: 2px;
  }
  .brand__name {
    display: block;
    font-weight: 800;
    font-size: 13px;
    letter-spacing: 1px;
    text-transform: uppercase;
    margin-top: 2px;
  }
  .card--front .brand { right: 40px; top: 36px; color: var(--red); }
  .card--back .brand { left: 40px; top: 168px; color: var(--white); }

  .front__rule {
    position: absolute;
    left: 40px; right: 40px; top: 150px;
    height: 1px; background: var(--rule);
  }
  .person { position: absolute; left: 40px; top: 178px; }
  .person__name { color: var(--red); font-weight: 600; font-size: 17px; }
  .person__role { color: var(--white); font-size: 13px; margin-top: 2px; }
  .person__rule { width: 200px; height: 1px; background: var(--rule); margin: 6px 0 5px; }
  .contact { list-style: none; }
  .contact li {
    display: flex; align-items: center; gap: 8px;
    color: var(--white); font-size: 12px; line-height: 19px;
  }
  .contact svg { width: 11px; height: 11px; fill: var(--red); flex: none; }

  .social-badge {
    position: absolute; left: 40px; top: 30px;
    width: 40px; height: 20px; background: var(--red);
  }
  .camera-photo {
    position: absolute; right: 0; top: 0;
    width: 300px; height: 200px;
    background: radial-gradient(ellipse at 55% 45%, #6b6b6b 0%, #3a3a3a 40%, #111111 75%);
  }
  .back__url {
    position: absolute; left: 40px; top: 245px;
    color: var(--white); font-size: 12px;
  }
</style>
</head>
<body>
  <section class="card card--front" aria-label="Card front">
    <div class="brand">
      <span class="brand__initials">KPH</span>
      <span class="brand__name">Kestrel Picture House</span>
    </div>
    <div class="front__rule"></div>
    <div class="person">
      <p class="person__name">Teodoro Valbuena</p>
      <p class="person__role">Producer/Writer/Director</p>
      <div class="person__rule"></div>
      <ul class="contact">
        <li>
          <svg viewBox="0 0 24 24"><path d="M6.6 10.8a15 15 0 0 0 6.6 6.6l2.2-2.2c.3-.3.7-.4 1-.2 1.1.4 2.3.6 3.6.6.6 0 1 .4 1 1V20c0 .6-.4 1-1 1A17 17 0 0 1 3 4c0-.6.4-1 1-1h3.5c.6 0 1 .4 1 1 0 1.3.2 2.5.6 3.6.1.3 0 .7-.2 1z"/></svg>
          555 014 2287
        </li>
        <li>
          <svg viewBox="0 0 24 24"><path d="M2 5h20v14H2zM4 7v.5l8 5 8-5V7l-8 5z"/></svg>
          hello@kestrelpicturehouse.example
        </li>
        <li>
          <svg viewBox="0 0 24 24"><circle cx="12" cy="12" r="10"/></svg>
          www.kestrelpicturehouse.example
        </li>
      </ul>
    </div>
  </section>

  <section class="card card--back" aria-label="Card back">
    <div class="social-badge"></div>
    <div class="camera-photo" role="img" aria-label="Photograph of a professional cinema camera rig"></div>
    <div class="brand">
      <span class="brand__initials">KPH</span>
      <span class="brand__name">Kestrel Picture House</span>
    </div>
    <p class="back__url">www.kestrelpicturehouse.example</p>
  </section>
</body>
</html>
```